Brightwell Supports

We need an updated website that captures the comprehensive services and supports we provide to persons with developmental disabilities. We need a website design that educates families about the services we provide. We would also need a website that is user-friendly so that we could periodically update training schedules and ongoing programming.

• Thank you for submitting designs.  A few things I am hoping to see offered in the website:
• Front page highlights the services we offer (host homes, family caregiver, day program, employment program, SLS program, supported apartment program, behavior/clinical program)
• Front page also highlights any new programs we want to make prominent:  family caregiver, future restaurant employment openings, etc...
• Interactive Training Calendar
• Employee Resources page (link to carevo, email login, etc.)
• Uniform provider application for host home providers
• Information on agency - history, goals, etc.
• Contact Information/Location

 

Fun things to include:

• Client Highlights (featuring a client story each month, etc...)
• Employee highlights (featuring a staff member...)
• link to other Brightwell business pages (Brightwell Therapy and Brightwell Restaurant)

```html
<!DOCTYPE html>
<html lang="en">
<head>
<meta charset="utf-8">
<title>Brightwell Supports</title>
<link rel="stylesheet" href="https://fonts.googleapis.com/css2?family=Open+Sans:wght@400;600&family=Roboto+Slab:wght@400&family=Fira+Sans+Condensed:wght@300&display=swap">
<style>
  :root {
    --brand-red: #8a2a2c;
    --brand-red-dark: #6e1d20;
    --ink: #3a3a3a;
    --text-muted: #7c7c7c;
    --rule: #d8d8d8;
    --panel-grey: #e2e2e2;
    --panel-grey-light: #efefef;
    --white: #ffffff;
  }
  * { box-sizing: border-box; margin: 0; padding: 0; }
  html, body { width: 1022px; height: 1200px; overflow: hidden; background: var(--white); }
  body { position: relative; font-family: "Open Sans", sans-serif; color: var(--ink); }

  .top-strip { position: absolute; left: 0; top: 0; width: 1022px; height: 3px; background: var(--brand-red); }

  .brand { position: absolute; left: 86px; top: 44px; display: flex; align-items: center; gap: 10px; }
  .brand-dot { width: 22px; height: 22px; border-radius: 50%; background: var(--brand-red); }
  .brand-name { font-family: "Open Sans", sans-serif; font-weight: 600; font-size: 24px; color: var(--ink); letter-spacing: 0.2px; }

  .phone { position: absolute; left: 490px; top: 50px; display: flex; align-items: center; }
  .phone svg { width: 28px; height: 36px; }
  .phone-divider { width: 1px; height: 38px; background: var(--rule); margin: 0 14px 0 12px; }
  .phone-numbers { font-family: "Fira Sans Condensed", sans-serif; font-weight: 300; font-size: 13px; line-height: 18px; color: var(--text-muted); }

  .search { position: absolute; left: 734px; top: 56px; width: 203px; height: 27px; display: flex; }
  .search-field { flex: 1; border: 1px solid #cfcfcf; border-right: none; font-size: 10px; color: #9a9a9a; padding: 7px 9px; }
  .search-button { width: 30px; background: var(--brand-red); display: flex; align-items: center; justify-content: center; }

  .main-nav { position: absolute; left: 86px; top: 128px; width: 851px; height: 34px; background: var(--brand-red); display: flex; }
  .main-nav a { color: var(--white); text-decoration: none; font-size: 11.2px; line-height: 34px; padding: 0 14.5px; white-space: nowrap; }
  .main-nav a.is-current { background: var(--brand-red-dark); padding: 0 19px; }

  .hero { position: absolute; left: 86px; top: 162px; width: 851px; height: 392px; background: linear-gradient(100deg, #d9c8b8 0%, #c7b3a1 30%, #9fb4cc 45%, #d7cfc6 65%, #b59a86 85%, #6f5a4e 100%); }
  .hero-arrow { position: absolute; top: 336px; width: 26px; height: 26px; border-radius: 50%; display: flex; align-items: center; justify-content: center; }
  .hero-arrow.prev { left: 28px; background: rgba(138,42,44,0.35); }
  .hero-arrow.next { left: 794px; background: rgba(70,70,70,0.75); }
  .hero-tagline { position: absolute; left: 101px; color: var(--white); font-size: 17.5px; font-weight: 600; letter-spacing: 0.6px; height: 30px; line-height: 30px; padding: 0 21px; }
  .hero-tagline.one { top: 215px; background: rgba(138,42,44,0.85); }
  .hero-tagline.two { top: 251px; background: rgba(110,52,58,0.85); }
  .hero-tagline.three { top: 285px; background: rgba(64,40,44,0.85); }

  .section-title { position: absolute; font-size: 15.5px; font-weight: 400; color: #4a4a4a; letter-spacing: 0.3px; }
  .section-rule { position: absolute; height: 5px; border-top: 1px dotted #cfcfcf; border-bottom: 1px dotted #cfcfcf; }

  .welcome-photo { position: absolute; left: 87px; top: 655px; width: 197px; height: 167px; background: linear-gradient(90deg, #c9cdd2 0%, #b9b4ae 45%, #d7c1ae 70%, #c9c7c6 100%); }
  .body-copy { font-family: Arial, sans-serif; font-size: 11.4px; line-height: 15.4px; color: var(--text-muted); text-align: justify; position: absolute; }

  .services { position: absolute; left: 634px; top: 655px; width: 304px; }
  .service-open { background: linear-gradient(#8e2c2f, #6e1d20); color: var(--white); height: 33px; line-height: 33px; padding: 0 16px; font-size: 12px; position: relative; }
  .service-body { border: 1px solid #e4e4e4; border-top: none; padding: 11px 16px 14px; font-family: Arial, sans-serif; font-size: 11.2px; line-height: 15.4px; color: var(--text-muted); text-align: justify; }
  .service-item { height: 32px; line-height: 32px; padding: 0 16px; font-size: 11.8px; color: #6a6a6a; background: linear-gradient(var(--panel-grey-light), var(--panel-grey)); border-bottom: 1px solid #fff; position: relative; }
  .service-item svg, .service-open svg { position: absolute; right: 14px; top: 12px; }

  .clients-title { position: absolute; left: 0; width: 1022px; top: 962px; text-align: center; font-family: "Roboto Slab", serif; font-size: 15.5px; color: #555; }
  .client-card { position: absolute; top: 1007px; width: 119px; height: 71px; border: 1px solid #dedede; display: flex; align-items: center; justify-content: center; gap: 5px; font-size: 11px; font-weight: 600; color: #666; }
  .client-mark { width: 9px; height: 9px; border-radius: 50%; background: #bdbdbd; }

  .site-footer { position: absolute; left: 0; top: 1139px; width: 1022px; height: 61px; background: var(--brand-red); color: var(--white); }
  .copyright { position: absolute; left: 86px; top: 22px; font-size: 11.3px; }
  .social-links { position: absolute; right: 80px; top: 23px; display: flex; gap: 14px; font-size: 10.5px; }
  .social-links a { color: var(--white); text-decoration: none; }
</style>
</head>
<body>
  <div class="top-strip"></div>

  <header>
    <div class="brand"><span class="brand-dot"></span><span class="brand-name">Brightwell Supports</span></div>

    <div class="phone">
      <svg viewBox="0 0 28 36" aria-hidden="true"><path d="M7 2 L12 9 L9 13 C10 18 13 23 17 26 L21 23 L27 29 L22 34 C12 32 3 20 3 7 Z" fill="#8a2a2c"/></svg>
      <span class="phone-divider"></span>
      <div class="phone-numbers">+(1) 555 204 1180<br>+(1) 555 204 1192</div>
    </div>

    <form class="search">
      <div class="search-field">Enter keyword</div>
      <div class="search-button">
        <svg width="14" height="14" viewBox="0 0 14 14" aria-hidden="true"><circle cx="6" cy="6" r="4.5" fill="none" stroke="#fff" stroke-width="1.8"/><line x1="9.3" y1="9.3" x2="13" y2="13" stroke="#fff" stroke-width="2"/></svg>
      </div>
    </form>

    <nav class="main-nav">
      <a class="is-current" href="#">Home</a>
      <a href="#">Services</a>
      <a href="#">Residential Program</a>
      <a href="#">Become a Provider</a>
      <a href="#">Meet Our Team!</a>
      <a href="#">Activity Calendar</a>
      <a href="#">Training Calendar</a>
      <a href="#">Contact Us</a>
    </nav>
  </header>

  <section class="hero" role="img" aria-label="Photo of smiling colleagues talking together around a table in a bright office">
    <div class="hero-arrow prev"><svg width="10" height="12" viewBox="0 0 10 12" aria-hidden="true"><path d="M7 1 L2 6 L7 11" fill="none" stroke="#fff" stroke-width="2"/></svg></div>
    <div class="hero-arrow next"><svg width="10" height="12" viewBox="0 0 10 12" aria-hidden="true"><path d="M3 1 L8 6 L3 11" fill="none" stroke="#fff" stroke-width="2"/></svg></div>
    <div class="hero-tagline one">Building Abilities</div>
    <div class="hero-tagline two">Creating Opportunities</div>
    <div class="hero-tagline three">Developing Relationships</div>
  </section>

  <h2 class="section-title" style="left:87px; top:596px;">WELCOME TO BRIGHTWELL SUPPORTS</h2>
  <div class="section-rule" style="left:87px; top:626px; width:494px;"></div>

  <div class="welcome-photo" role="img" aria-label="Portrait photo of a smiling staff member in a suit"></div>
  <p class="body-copy" style="left:301px; top:666px; width:281px;">Brightwell Supports is an agency designed to creatively serve individuals with developmental disabilities in community-based settings throughout Colorado. Brightwell Supports is an approved service agency through the Division of Developmental Disabilities. Many desktop publishing packages and web page edi-tors now use Lorem Ipsum as</p>
  <p class="body-copy" style="left:301px; top:789px; width:281px;">&nbsp;their default model text, and a Well being of our clients first! search for 'lorem</p>
  <p class="body-copy" style="left:87px; top:836px; width:495px;">established fact that a reader will be distracted by the readable content of a page when looking at its layout. The point of using Lorem Ipsum is that it has a more-or-less normal distribution of</p>

  <h2 class="section-title" style="left:635px; top:596px;">OUR SERVICES</h2>
  <div class="section-rule" style="left:635px; top:626px; width:303px;"></div>

  <div class="services">
    <div class="service-open">Host Home Services
      <svg width="8" height="7" viewBox="0 0 8 7" aria-hidden="true"><path d="M0 0 H8 L4 7 Z" fill="#e5c4c4"/></svg>
    </div>
    <div class="service-body">Distribution of letters, as opposed to using 'Content here, content here', making it look like readable Eng-lish. Many desktop many web sites still in their infancy.</div>
    <div class="service-item">Respite Services<svg width="7" height="8" viewBox="0 0 7 8" aria-hidden="true"><path d="M7 0 V8 L0 4 Z" fill="#888"/></svg></div>
    <div class="service-item">Mentor Services<svg width="7" height="8" viewBox="0 0 7 8" aria-hidden="true"><path d="M7 0 V8 L0 4 Z" fill="#888"/></svg></div>
    <div class="service-item">Supported Employment Services<svg width="7" height="8" viewBox="0 0 7 8" aria-hidden="true"><path d="M7 0 V8 L0 4 Z" fill="#888"/></svg></div>
    <div class="service-item">SLS Services<svg width="7" height="8" viewBox="0 0 7 8" aria-hidden="true"><path d="M7 0 V8 L0 4 Z" fill="#888"/></svg></div>
  </div>

  <h2 class="clients-title">Some of our Clients who love being with us!</h2>
  <div class="client-card" style="left:87px;"><span class="client-mark"></span>Orchard Lane</div>
  <div class="client-card" style="left:234px;"><span class="client-mark"></span>Tidemark</div>
  <div class="client-card" style="left:380px;"><span class="client-mark"></span>Fernhill</div>
  <div class="client-card" style="left:527px;"><span class="client-mark"></span>Lumen Works</div>
  <div class="client-card" style="left:674px;"><span class="client-mark"></span>Arcwise Studio</div>
  <div class="client-card" style="left:821px;"><span class="client-mark"></span>Relay North</div>

  <footer class="site-footer">
    <p class="copyright">© Copyright&nbsp; 2014 Brightwell Support. All rights reserved</p>
    <div class="social-links">
      <a href="#">Circlet</a><a href="#">Chirpline</a><a href="#">Plusroom</a><a href="#">Pinboard</a>
    </div>
  </footer>
</body>
</html>
```